Blow Dry Bar Business Cards

These cards must be eye catching and modern.
You must be willing to work fast and make changes.

Winner will be offered other projects

Files 1 THIS IS THE STYLE CARDS I AM INTRESTED IN!!!
Please be creative, I am paying for my own eye catching design. I need files to be nexa press ready.

COLORS THAT ARE PAINTED INSIDE MY SHOP:
- - - http://www.quorvelpaint.example/en/explore-colors/painter/color-selector.html?colors=4007-3C

- - - http://www.brandivex.example/color/paint-colors/hidden-corridor-d58-2

I want the business cards sleek and modern if you use the logo please correct imperfections. I added the part that says Blow Dry Bar (see website).
Do not be afraid to separate the blow dryer from the name to make the cards look like the file with the pink elephant.

SHOULD INCLUDE
*Blow Dryer (we are a blow dry bar not a salon we do not cut or color so do not include sheers of any kind)
*BUSINESS NAME: Simply Swept Upward - Blow Dry Bar (PLEASE SEE MY WEBSITE)
* Website: SIMPLYSWEPTUPWARD.EXAMPLE
*Phone number (555) 014-2763
Updates

Nexa press said it can be submitted in JPG

http://www.brandivex.example/color/paint-colors/hidden-corridor-d58-2 http://www.quorvelpaint.example/en/explore-colors/painter/color-selector.html?colors=4007-3C ^^^^ These links will take you to the color paint that is painted inside my shop.

Target Market(s)

AGES 18 - 55 WOMEN
HIGH END MARKET

Industry/Entity Type

Salon

Requirements
Must have
• SEE COLOR EXAMPLE FILE
BLOW DRYER
UNIQUE
I LIKE THE CARD WITH THE PINK ELEPHANT THE BEST
Nice to have
• BE AS CREATIVE AND MODERN AS POSSIBLE DO NOT COPY ANY OF THE CARDS BELOW.
Should not have
• SCISSORS
PINK

```html
<!DOCTYPE html>
<html lang="en">
<head>
<meta charset="utf-8">
<title>Swept Upward – Business Cards</title>
<link href="https://fonts.googleapis.com/css2?family=Arvo:wght@400&family=Arimo:wght@400&display=swap" rel="stylesheet">
<style>
  :root {
    --stage: #e9e6e2;
    --card-black: #0b0b0b;
    --card-glow: #3a3a3a;
    --card-white: #ffffff;
    --ink-white: #ffffff;
    --ink-black: #141414;
    --accent-yellow: #e6cf1c;
    --card-shadow: rgba(0,0,0,0.22);
  }
  * { margin: 0; padding: 0; box-sizing: border-box; }
  html, body { width: 1200px; height: 914px; overflow: hidden; }
  body { background: var(--stage); position: relative; }

  .card {
    position: absolute;
    width: 600px;
    height: 343px;
    box-shadow: 0 10px 28px var(--card-shadow);
  }
  .card--back {
    left: 540px; top: 100px;
    background: var(--card-white);
  }
  .card--front {
    left: 60px; top: 470px;
    background: radial-gradient(ellipse 70% 75% at 55% 60%, var(--card-glow) 0%, #161616 55%, var(--card-black) 100%);
  }

  .brand-lockup {
    position: absolute;
    display: flex;
    align-items: flex-end;
    gap: 18px;
  }
  .card--back .brand-lockup { right: 48px; top: 170px; }
  .card--front .brand-lockup { right: 48px; top: 36px; }

  .brand-name {
    font-family: "Arvo", serif;
    font-weight: 400;
    font-size: 48px;
    line-height: 1;
    letter-spacing: 0.5px;
    white-space: nowrap;
  }
  .card--back .brand-name { color: var(--ink-black); }
  .card--front .brand-name { color: var(--ink-white); }

  .brand-mark {
    width: 62px;
    height: 62px;
    flex: none;
    margin-bottom: -14px;
  }
  .card--back .brand-mark { background: var(--ink-black); }
  .card--front .brand-mark { background: var(--ink-white); }

  .contact-list {
    position: absolute;
    left: 56px; top: 140px;
    list-style: none;
    font-family: "Arimo", sans-serif;
    font-size: 19px;
    line-height: 27px;
    color: var(--accent-yellow);
    text-transform: uppercase;
  }
  .contact-list li { display: flex; align-items: center; gap: 12px; }
  .contact-list .no-icon { padding-left: 30px; }
  .contact-icon { width: 18px; height: 18px; flex: none; fill: var(--accent-yellow); }
</style>
</head>
<body>

  <section class="card card--back" aria-label="Business card back">
    <div class="brand-lockup">
      <div class="brand-name">Swept Upward</div>
      <div class="brand-mark" role="img" aria-label="Blow dryer brand mark"></div>
    </div>
  </section>

  <section class="card card--front" aria-label="Business card front">
    <div class="brand-lockup">
      <div class="brand-name">Swept Upward</div>
      <div class="brand-mark" role="img" aria-label="Blow dryer brand mark"></div>
    </div>
    <ul class="contact-list">
      <li>
        <svg class="contact-icon" viewBox="0 0 24 24" aria-hidden="true"><path d="M6.6 10.8a15.1 15.1 0 0 0 6.6 6.6l2.2-2.2c.3-.3.7-.4 1-.2 1.1.4 2.3.6 3.6.6.6 0 1 .4 1 1V20c0 .6-.4 1-1 1A17 17 0 0 1 3 4c0-.6.4-1 1-1h3.5c.6 0 1 .4 1 1 0 1.3.2 2.5.6 3.6.1.3 0 .7-.2 1z"/></svg>
        <span>(555) 014-2763</span>
      </li>
      <li>
        <svg class="contact-icon" viewBox="0 0 24 24" aria-hidden="true"><path d="M12 2a10 10 0 1 0 0 20 10 10 0 0 0 0-20zm6.9 6h-3a15.6 15.6 0 0 0-1.3-3.9A8 8 0 0 1 18.9 8zM12 4c.8 1.2 1.5 2.5 1.9 4h-3.8c.4-1.5 1.1-2.8 1.9-4zM4.3 14a8.2 8.2 0 0 1 0-4h3.4a16.5 16.5 0 0 0 0 4zm.8 2h3a15.6 15.6 0 0 0 1.3 3.9A8 8 0 0 1 5.1 16zm3-8h-3a8 8 0 0 1 4.3-3.9C8.8 5.3 8.4 6.6 8.1 8zM12 20c-.8-1.2-1.5-2.5-1.9-4h3.8c-.4 1.5-1.1 2.8-1.9 4zm2.3-6H9.7a14.7 14.7 0 0 1 0-4h4.6a14.7 14.7 0 0 1 0 4zm.3 5.9c.6-1.2 1-2.5 1.3-3.9h3a8 8 0 0 1-4.3 3.9zm1.7-5.9a16.5 16.5 0 0 0 0-4h3.4a8.2 8.2 0 0 1 0 4z"/></svg>
        <span>www.simplysweptupward.example</span>
      </li>
      <li>
        <svg class="contact-icon" viewBox="0 0 24 24" aria-hidden="true"><path d="M2 5h20v14H2zm2 2v.5l8 5 8-5V7zm0 2.8V17h16V9.8l-8 5z"/></svg>
        <span>info@simplysweptupward.example</span>
      </li>
      <li>
        <svg class="contact-icon" viewBox="0 0 24 24" aria-hidden="true"><path d="M12 2a7 7 0 0 0-7 7c0 5.2 7 13 7 13s7-7.8 7-13a7 7 0 0 0-7-7zm0 9.5A2.5 2.5 0 1 1 12 6.5a2.5 2.5 0 0 1 0 5z"/></svg>
        <span>210 Harbor Pine Drive Suite 11</span>
      </li>
      <li class="no-icon"><span>Maple Ridge, Texas 75501</span></li>
    </ul>
  </section>

</body>
</html>
```